Flat bootstrap design for existing site

I'm looking for a modern flat design based around an existing logo. This has to be a custom design (no external templates), and implemented into a bootstrap framework.

The logo is attached as 2 versions - choose whichever you want, that flows better with whatever design you choose.

Added screenshots of the existing site (currently using the default bootstrap layouts). Please make your designs around those pages in the screenshots (i.e. the homepage only has the postal code input and the header). The active page has 3 screenshots, because I wanted to illustrate the other states that would be visible (in the table rows).

This is a moving/junk removal website, just for some context.

Here's some example websites (flat designs) that I like, just to give you an idea of what I'm after.

https://www.plimvora.com/
https://dacklow.com/
https://trevanu.com/
https://quobrintal.com/en/

Coding

Coded - Design and coding required

Number of Pages Required

5+ page

Colors

Designer to choose colors to be used in the design.

Requirements
Must have
• It must be a modern/simple flat design, that is built around the existing logo (attached).
• It has to be implemented using bootstrap.

```html
<!DOCTYPE html>
<html lang="en">
<head>
<meta charset="utf-8">
<title>Haulvex — Junk Removal</title>
<link rel="stylesheet" href="https://fonts.googleapis.com/css2?family=Raleway:wght@400;500;700;800&display=swap">
<style>
  :root {
    --sky-top: #6ae3f8;
    --sky-mid: #56d6f4;
    --street: #41c1ef;
    --accent: #3ec4f1;
    --white: #ffffff;
    --ink-muted: #a3a3a3;
    --sign-in: #6a6a6a;
    --footer: #060606;
    --social: #3a3a3a;
  }
  * { box-sizing: border-box; margin: 0; padding: 0; }
  html, body { width: 1200px; height: 675px; overflow: hidden; }
  body { font-family: "Raleway", sans-serif; background: var(--footer); position: relative; }

  .hero {
    position: absolute; left: 0; top: 0; width: 1200px; height: 585px;
    background: linear-gradient(180deg, var(--sky-top) 0%, var(--sky-mid) 62%, var(--street) 100%);
  }
  .hero-scene {
    position: absolute; left: 0; top: 0; width: 100%; height: 100%;
    background: linear-gradient(180deg, rgba(255,255,255,0) 0%, rgba(255,255,255,0) 55%, rgba(60,170,235,0.25) 56%, rgba(60,170,235,0.25) 94%, rgba(55,185,238,0.5) 94%);
  }

  .brand {
    position: absolute; left: 86px; top: 28px;
    font-size: 38px; font-weight: 800; color: var(--white); letter-spacing: 1px;
  }

  .main-nav { position: absolute; top: 35px; right: 87px; display: flex; align-items: center; }
  .main-nav a {
    color: var(--white); text-decoration: none; font-size: 14px; font-weight: 500;
    margin-left: 40px; letter-spacing: 0.2px;
  }
  .main-nav a:first-child { margin-left: 0; }
  .main-nav .sign-in {
    background: var(--sign-in); height: 28px; padding: 0 13px; line-height: 28px;
    border-radius: 3px; font-size: 15px; box-shadow: 0 2px 4px rgba(0,0,0,0.25);
  }

  .hero-title {
    position: absolute; left: 0; width: 100%; top: 262px; text-align: center;
    font-size: 46px; font-weight: 700; color: var(--white); letter-spacing: 0.2px;
  }

  .booking { position: absolute; top: 343px; left: 337px; display: flex; gap: 12px; }
  .booking .postal {
    width: 345px; height: 60px; border: none; border-radius: 3px; background: var(--white);
    font-family: "Raleway", sans-serif; font-size: 18px; font-weight: 700; padding: 0 33px;
    color: #555; box-shadow: 0 2px 6px rgba(0,0,0,0.12);
  }
  .booking .postal::placeholder { color: var(--ink-muted); }
  .booking .book-btn {
    width: 169px; height: 60px; border: none; border-radius: 3px; background: var(--accent);
    color: var(--white); font-family: "Raleway", sans-serif; font-size: 17px; font-weight: 800;
    box-shadow: 0 2px 6px rgba(0,0,0,0.12);
  }

  .site-footer {
    position: absolute; left: 0; top: 585px; width: 1200px; height: 90px; background: var(--footer);
  }
  .copyright {
    position: absolute; left: 86px; top: 36px; color: var(--white); font-size: 13px; font-weight: 400;
  }
  .social { position: absolute; left: 970px; top: 32px; display: flex; gap: 7px; }
  .social span { width: 23px; height: 23px; border-radius: 50%; background: var(--social); display: block; }
</style>
</head>
<body>
  <header class="hero">
    <div class="hero-scene" role="img" aria-label="Flat blue illustration of a city street with buildings, a brick wall, waste bins and a garbage truck"></div>
    <div class="brand">HAULVEX</div>
    <nav class="main-nav">
      <a href="#">BOOK</a>
      <a href="#">HOW IT WORKS</a>
      <a href="#">BECOME A DRIVER</a>
      <a href="#" class="sign-in">SIGN IN</a>
    </nav>
    <h1 class="hero-title">Need junk removed? Book now.</h1>
    <form class="booking">
      <input class="postal" type="text" placeholder="Postal Code">
      <button class="book-btn" type="button">BOOK</button>
    </form>
  </header>
  <footer class="site-footer">
    <p class="copyright">2017 © Haulvex. All rights reserved.</p>
    <div class="social" aria-label="Social links">
      <span></span><span></span><span></span><span></span><span></span>
    </div>
  </footer>
</body>
</html>
```